Compnay PowerPoint Tempalte Design

I am needing a good base design and slide designs for interior and exterior company presentations. The template will need to be on the company brand with proper coloring and fonts. Able to be creative with layout options with a good example attached.
website for reference: www.crewvlt.com/

Target Market(s)

Professionals

Font styles to use
Other font styles liked:
• Helvetica

Requirements
Must have
• On Brand Colors, Clean, simple design

```html
<!DOCTYPE html>
<html lang="en">
<head>
<meta charset="utf-8">
<title>CREWVLT Presentation Template</title>
<link href="https://fonts.googleapis.com/css2?family=Arimo:ital,wght@0,400;0,700;1,400;1,700&display=swap" rel="stylesheet">
<style>
:root{
  --green:#6cc22b;
  --green-light:#9bd65a;
  --cyan:#8fdde8;
  --cyan-soft:#bfeaf0;
  --blue:#3aa3e3;
  --navy:#0f5c87;
  --ink:#141414;
  --panel:#111517;
  --text:#222;
  --paper:#ffffff;
  --page:#ffffff;
}
*{box-sizing:border-box;margin:0;padding:0}
html,body{width:1200px;height:4093px;overflow:hidden;background:var(--page);font-family:"Arimo",Helvetica,Arial,sans-serif;color:var(--text)}
.deck{position:relative;width:1200px;height:4093px}
.slide{position:absolute;left:40px;width:1128px;height:635px;overflow:hidden;background:var(--paper);box-shadow:0 1px 4px rgba(0,0,0,.25)}
.slide > *{position:absolute}
.shapes{left:0;top:0;width:1128px;height:635px}
.photo{left:0;top:0;width:1128px;height:635px}
.brand{font-weight:700;color:var(--ink);letter-spacing:1px}
.brand-mark{display:inline-block;width:14px;height:14px;background:var(--navy);margin-right:8px;vertical-align:middle}
.slide-title{font-weight:700;color:var(--ink);font-size:42px}

/* cover */
.cover .brand{left:56px;top:255px;font-size:58px}
.cover .headline{left:56px;top:330px;font-size:42px;line-height:63px;font-weight:700;color:var(--ink);width:520px}

/* about */
.about .bg-photo{left:0;top:147px;width:1128px;height:488px;background:linear-gradient(120deg,#e8eaea,#d7dbdb 55%,#eceeee)}
.about .slide-title{left:51px;top:48px;font-size:40px}
.about .brand{right:40px;top:85px;font-size:28px}
.about .body{left:72px;top:180px;width:690px;font-size:16.5px;line-height:37px;color:#222}

/* what we do */
.services{background:linear-gradient(180deg,#6cc22b 0%,#8fd166 40%,#a7e3d8 75%,#a3dfe9 100%)}
.services .slide-title{left:75px;top:125px;font-size:66px;font-weight:700}
.services .brand{right:40px;top:90px;font-size:28px}
.service{top:234px;width:317px;height:260px;background:var(--panel);display:flex;flex-direction:column;align-items:center;justify-content:center;gap:18px;color:#fff;font-weight:700;font-size:22px}
.service svg{width:56px;height:56px}

/* values */
.values .slide-title{left:50px;top:105px}
.values .brand{right:25px;top:75px;font-size:26px;color:#2f6b6b}
.values .intro{left:50px;top:168px;width:560px;font-size:11.5px;line-height:21px;color:#222}
.value{left:50px;width:420px;height:80px}
.value .icon{position:absolute;left:0;top:0;width:74px;height:74px;border-radius:50%;background:radial-gradient(circle,#7ecc4a 0 48%,#d9f1c4 50% 100%);display:flex;align-items:center;justify-content:center}
.value .icon svg{width:38px;height:38px}
.value h3{position:absolute;left:90px;top:3px;font-size:19px;font-weight:400;color:#111}
.value p{position:absolute;left:90px;top:30px;width:240px;font-size:9.5px;line-height:18px;color:#333}

/* testimonials */
.testimonials{background:var(--navy)}
.testimonials .brand{left:36px;top:88px;font-size:26px;color:#fff}
.testimonials .slide-title{left:0;width:1128px;text-align:center;top:68px}
.testimonials .quote-mark{left:0;width:1128px;text-align:center;top:108px;font-size:120px;font-weight:700;line-height:1;color:var(--green);font-family:Georgia,serif}
.testimonials .quote{left:314px;width:500px;top:250px;text-align:center;font-style:italic;font-weight:700;font-size:20px;line-height:44px;color:#444}

/* contact */
.contact .brand{left:32px;top:80px;font-size:26px}
.contact .slide-title{left:50px;top:150px}
.contact .intro{left:50px;top:210px;width:380px;font-size:11.5px;line-height:21px}
.contact-item{left:50px;width:400px}
.contact-item .icon{position:absolute;left:0;top:0;width:74px;height:74px;border-radius:50%;background:radial-gradient(circle,#7ecc4a 0 48%,#d9f1c4 50% 100%);display:flex;align-items:center;justify-content:center}
.contact-item .icon svg{width:36px;height:36px}
.contact-item h3{position:absolute;left:90px;top:2px;font-size:19px;font-weight:400;color:#111}
.contact-item p{position:absolute;left:90px;top:30px;font-size:10px;line-height:18px;color:#222;text-transform:uppercase}
.contact-item p.lower{text-transform:none}
</style>
</head>
<body>
<main class="deck">

  <!-- Cover -->
  <section class="slide cover" style="top:43px">
    <div class="photo" role="img" aria-label="Sunlit forest path with autumn trees" style="background:linear-gradient(160deg,#3d5a2a,#7a8d3b 35%,#c2521f 65%,#5b3a1c);clip-path:polygon(712px 0,1128px 0,1128px 635px,496px 635px)"></div>
    <svg class="shapes" viewBox="0 0 1128 635" aria-hidden="true">
      <defs>
        <linearGradient id="cv-band" x1="0" y1="0" x2="0" y2="1"><stop offset="0" stop-color="#6cc22b"/><stop offset="1" stop-color="#8fdde8"/></linearGradient>
      </defs>
      <polygon points="560,0 700,0 430,635 330,635" fill="url(#cv-band)" opacity=".95"/>
      <polygon points="660,160 760,160 560,635 470,635" fill="#8fdde8" opacity=".6"/>
      <polygon points="690,200 750,200 660,410 600,410" fill="#3aa3e3" opacity=".45"/>
    </svg>
    <div class="brand"><span class="brand-mark"></span>CREWVLT</div>
    <h1 class="headline">Neque porro quisquam est qui dolorem ipsum quia dolor</h1>
  </section>

  <!-- About -->
  <section class="slide about" style="top:717px">
    <div class="bg-photo" role="img" aria-label="Faded photo of smiling team members"></div>
    <svg class="shapes" viewBox="0 0 1128 635" aria-hidden="true">
      <defs>
        <linearGradient id="ab-band" x1="0" y1="0" x2="1" y2="0"><stop offset="0" stop-color="#bfeaf0"/><stop offset=".5" stop-color="#a6e0b0"/><stop offset="1" stop-color="#8fd44f"/></linearGradient>
      </defs>
      <polygon points="0,0 803,0 728,147 0,147" fill="url(#ab-band)"/>
      <polygon points="1080,410 1128,410 1128,500 1040,635 980,635" fill="#6cc22b"/>
      <polygon points="1090,540 1128,540 1128,635 1050,635" fill="#3aa3e3" opacity=".85"/>
    </svg>
    <div class="photo" role="img" aria-label="Two team members laughing together" style="background:linear-gradient(135deg,#6b4a3a,#2f2520 50%,#a38c78);clip-path:polygon(790px 275px,1100px 275px,930px 635px,660px 635px)"></div>
    <h2 class="slide-title">ABOUT US</h2>
    <div class="brand"><span class="brand-mark"></span>CREWVLT</div>
    <p class="body">CREWVLT is dedicated to cultivating a positive culture of leadership for its team members' professional and personal development, and this person-focused mentality transfers throughout the company from partners to our teams to guests. We strive to ensure each team member feels valued in all aspects of their role, reinforcing the importance of fostering a self-sustaining culture of success where everyone makes a team effort to communicate and overcome adversity.</p>
  </section>

  <!-- What we do -->
  <section class="slide services" style="top:1390px">
    <svg class="shapes" viewBox="0 0 1128 635" aria-hidden="true">
      <polygon points="650,0 700,0 580,180 530,180" fill="#bfeaf0" opacity=".8"/>
      <polygon points="710,0 760,0 640,180 590,180" fill="#3aa3e3" opacity=".8"/>
      <polygon points="770,0 830,0 700,180 650,180" fill="#8fdde8" opacity=".6"/>
      <polygon points="300,360 380,360 250,635 170,635" fill="#3aa3e3" opacity=".55"/>
      <polygon points="230,430 290,430 180,635 120,635" fill="#bfeaf0" opacity=".6"/>
    </svg>
    <h2 class="slide-title">WHAT WE DO</h2>
    <div class="brand"><span class="brand-mark"></span>CREWVLT</div>
    <div class="service" style="left:75px">
      <svg viewBox="0 0 56 56" aria-hidden="true"><path d="M8 40h40" stroke="#7ecc4a" stroke-width="4" stroke-linecap="round"/><path d="M12 38a16 16 0 0 1 32 0z" fill="#7ecc4a"/><circle cx="28" cy="20" r="3" fill="#7ecc4a"/><circle cx="38" cy="10" r="4" fill="none" stroke="#7ecc4a" stroke-width="2.5"/><path d="M22 6c-3 4 3 6 0 10" stroke="#7ecc4a" stroke-width="2.5" fill="none"/></svg>
      Restaurants
    </div>
    <div class="service" style="left:405px">
      <svg viewBox="0 0 56 56" aria-hidden="true"><path d="M6 28L24 12l18 16" stroke="#7ecc4a" stroke-width="4" fill="none"/><rect x="12" y="28" width="24" height="16" fill="#7ecc4a"/><circle cx="42" cy="18" r="9" fill="#7ecc4a"/><text x="42" y="22" font-size="12" font-weight="700" fill="#111" text-anchor="middle" font-family="Arimo,sans-serif">$</text><path d="M20 46h28" stroke="#7ecc4a" stroke-width="4"/></svg>
      Real Estate
    </div>
    <div class="service" style="left:730px">
      <svg viewBox="0 0 56 56" aria-hidden="true"><circle cx="28" cy="22" r="16" fill="#7ecc4a"/><circle cx="28" cy="22" r="9" fill="#111"/><path d="M28 16l2 4 4 .5-3 3 1 4-4-2-4 2 1-4-3-3 4-.5z" fill="#7ecc4a"/><path d="M20 36l-5 14 6-3 4 5 3-14M36 36l5 14-6-3-4 5-3-14" fill="#7ecc4a"/></svg>
      Development
    </div>
  </section>

  <!-- Core values -->
  <section class="slide values" style="top:2064px">
    <div class="photo" role="img" aria-label="Team meeting around a table in a glass-walled office" style="background:linear-gradient(150deg,#9fc7c0,#4b6f6a 45%,#1f3b3a 80%);clip-path:polygon(696px 0,1128px 0,1128px 635px,440px 635px)"></div>
    <svg class="shapes" viewBox="0 0 1128 635" aria-hidden="true">
      <defs>
        <linearGradient id="va-band" x1="0" y1="0" x2="0" y2="1"><stop offset="0" stop-color="#6cc22b"/><stop offset="1" stop-color="#8fdde8"/></linearGradient>
      </defs>
      <polygon points="570,0 710,0 500,470 360,470" fill="url(#va-band)" opacity=".9"/>
      <polygon points="560,300 640,300 470,635 360,635" fill="#8fdde8" opacity=".75"/>
      <polygon points="600,200 660,200 560,420 500,420" fill="#3aa3e3" opacity=".4"/>
    </svg>
    <h2 class="slide-title">OUR CORE VALUES</h2>
    <div class="brand">CREWVLT</div>
    <p class="intro">Our culture is founded on four core values and the entrepreneurial spirit of ownership that comes from a foundation of passion for our people, commitment to our business, transparency, and continued progress.</p>
    <div class="value" style="top:230px">
      <div class="icon"><svg viewBox="0 0 38 38" aria-hidden="true"><circle cx="16" cy="12" r="6" fill="none" stroke="#0f5c87" stroke-width="2"/><path d="M5 32c0-7 5-11 11-11s8 2 9 4" fill="none" stroke="#0f5c87" stroke-width="2"/><path d="M28 22l6 2v5c0 3-3 5-6 6-3-1-6-3-6-6v-5z" fill="none" stroke="#0f5c87" stroke-width="2"/></svg></div>
      <h3>INTEGRITY</h3>
      <p>Integrity in everything we do. Do the right thing even when no one is looking.</p>
    </div>
    <div class="value" style="top:320px">
      <div class="icon"><svg viewBox="0 0 38 38" aria-hidden="true"><circle cx="19" cy="10" r="4" fill="none" stroke="#0f5c87" stroke-width="2"/><circle cx="10" cy="16" r="3" fill="none" stroke="#0f5c87" stroke-width="2"/><circle cx="28" cy="16" r="3" fill="none" stroke="#0f5c87" stroke-width="2"/><path d="M4 24c4 8 26 8 30 0" fill="none" stroke="#0f5c87" stroke-width="2"/></svg></div>
      <h3>FAMILY</h3>
      <p>Family first, always. All decisions must benefit our family and the company.</p>
    </div>
    <div class="value" style="top:410px">
      <div class="icon"><svg viewBox="0 0 38 38" aria-hidden="true"><path d="M19 5a10 10 0 0 0-6 18v4h12v-4a10 10 0 0 0-6-18z" fill="none" stroke="#0f5c87" stroke-width="2"/><path d="M14 31h10M16 35h6" stroke="#0f5c87" stroke-width="2"/></svg></div>
      <h3>ESPECT</h3>
      <p>We care for one another, praise efforts, recognize progress, and reward results.</p>
    </div>
    <div class="value" style="top:500px">
      <div class="icon"><svg viewBox="0 0 38 38" aria-hidden="true"><path d="M19 4c2 7 10 10 10 19a10 10 0 0 1-20 0c0-5 3-7 4-11 2 3 3 4 4 4-1-5 0-9 2-12z" fill="none" stroke="#0f5c87" stroke-width="2"/></svg></div>
      <h3>PASSION</h3>
      <p>We are positive, hardworking, and disciplined in all we do, which stems from our innate passion.</p>
    </div>
  </section>

  <!-- Testimonials -->
  <section class="slide testimonials" style="top:2738px">
    <svg class="shapes" viewBox="0 0 1128 635" aria-hidden="true">
      <polygon points="360,0 1010,0 760,635 120,635" fill="#f3f6f6"/>
      <polygon points="180,0 360,0 60,470 0,470 0,290" fill="#6cc22b"/>
      <polygon points="230,150 300,150 70,540 0,540 0,500" fill="#3aa3e3" opacity=".85"/>
      <polygon points="100,300 170,300 40,470 0,470 0,420" fill="#bfeaf0" opacity=".8"/>
      <polygon points="1010,0 1128,0 1128,100 940,470 880,470" fill="#6cc22b"/>
      <polygon points="1060,120 1110,120 860,635 790,635" fill="#3aa3e3" opacity=".85"/>
      <polygon points="1000,300 1040,300 910,470 860,470" fill="#8fdde8" opacity=".8"/>
    </svg>
    <div class="brand"><span class="brand-mark" style="background:#fff"></span>CREWVLT</div>
    <h2 class="slide-title">TESTIMONIALS</h2>
    <div class="quote-mark">&#8221;</div>
    <p class="quote">Lorem Ipsum is simply dummy text of the printing and typesetting industry. Lorem Ipsum has been the industry's standard dummy text ever since the 1500s, when an unknown printer took a galley of type and scrambled it to make a type specimen book.</p>
  </section>

  <!-- Contact -->
  <section class="slide contact" style="top:3411px">
    <div class="photo" role="img" aria-label="Mountain lake at sunset with a red canoe and autumn trees" style="background:linear-gradient(180deg,#5f6b78,#d39b5a 30%,#7c5a2a 55%,#c4703a 75%,#3e4a52);clip-path:polygon(700px 0,1128px 0,1128px 635px,480px 635px)"></div>
    <svg class="shapes" viewBox="0 0 1128 635" aria-hidden="true">
      <defs>
        <linearGradient id="ct-band" x1="0" y1="0" x2="0" y2="1"><stop offset="0" stop-color="#6cc22b"/><stop offset="1" stop-color="#8fdde8"/></linearGradient>
      </defs>
      <polygon points="560,0 690,0 430,600 300,600" fill="url(#ct-band)" opacity=".95"/>
      <polygon points="600,240 680,240 480,635 380,635" fill="#8fdde8" opacity=".7"/>
      <polygon points="640,330 690,330 600,520 550,520" fill="#3aa3e3" opacity=".4"/>
    </svg>
    <div class="brand"><span class="brand-mark"></span>CREWVLT</div>
    <h2 class="slide-title">CONTACT US</h2>
    <p class="intro">Lorem Ipsum is simply dummy text of the printing and typesetting industry. Lorem Ipsum has been the industry's</p>
    <div class="contact-item" style="top:285px">
      <div class="icon"><svg viewBox="0 0 36 36" aria-hidden="true"><path d="M18 3a10 10 0 0 0-10 10c0 8 10 19 10 19s10-11 10-19A10 10 0 0 0 18 3z" fill="#0f5c87"/><circle cx="18" cy="13" r="4" fill="#d9f1c4"/></svg></div>
      <h3>CREWVLT</h3>
      <p>4120 N. Ridgeline Ave<br>Suite 210<br>Denver, CO 80216</p>
    </div>
    <div class="contact-item" style="top:405px">
      <div class="icon"><svg viewBox="0 0 36 36" aria-hidden="true"><circle cx="18" cy="18" r="14" fill="#0f5c87"/><text x="18" y="24" font-size="17" font-weight="700" fill="#d9f1c4" text-anchor="middle" font-family="Arimo,sans-serif">@</text></svg></div>
      <h3>EMAIL</h3>
      <p class="lower">info@crewvlt.com</p>
    </div>
  </section>

</main>
</body>
</html>
```